New Candy Packaging Design

Looking to create an attractive design for modern retail for our single stick candy that will stand out on retail shelves. It will be hung from a whole. The design should have brand elements like the irregular shapes, bright pastel colors. Please visit plumcrestcandyworks.com to ensure the product could be an extension of the product range. 3 colors, pink(sakura flavor), green(muscat grape flavor), and blue(french vanilla flavor).

Target Market(s)

Millenias and Genz

Industry/Entity Type

Food

Requirements
Must have
• Look and feel of brand extension for Tindra, Matt finish
Nice to have
• fruit shapes
Should not have
• tacky design

```html
<!DOCTYPE html>
<html lang="en">
<head>
<meta charset="utf-8">
<title>Tindra Rock Sugar Sticks – Hang Tag Range</title>
<link rel="stylesheet" href="https://fonts.googleapis.com/css2?family=Alfa+Slab+One&family=Roboto+Slab:wght@400&family=Open+Sans:wght@400&display=swap">
<style>
  :root {
    --paper: #ffffff;
    --sakura-1: #e8559a;
    --sakura-2: #f03f8a;
    --sakura-3: #d62a73;
    --sakura-soft: #f27fb0;
    --grape-1: #9fcf3b;
    --grape-2: #79b12e;
    --grape-3: #4e8a22;
    --grape-soft: #b9de6a;
    --vanilla-1: #1499dc;
    --vanilla-2: #0f7fc1;
    --vanilla-3: #0c6aa4;
    --vanilla-soft: #f3efe2;
    --ink-light: #ffffff;
    --hole-dark: #1a1a1a;
    --window: #eeeeee;
    --stick: #d8b98a;
    --stick-end: #c9a677;
  }
  * { margin: 0; padding: 0; box-sizing: border-box; }
  html, body { width: 1200px; height: 461px; overflow: hidden; background: var(--paper); }
  .range { position: relative; width: 1200px; height: 461px; }
  .tag { position: absolute; top: 38px; width: 112.5px; height: 388px; display: block; }
  .tag text { fill: var(--ink-light); }
  .descriptor { font-family: "Roboto Slab", serif; font-size: 11px; }
  .brand-name { font-family: "Alfa Slab One", serif; font-size: 56px; }
  .tagline { font-family: "Open Sans", sans-serif; font-size: 17px; }
  .flavor-big { font-family: "Alfa Slab One", serif; font-size: 34px; }
  .flavor-small { font-family: "Alfa Slab One", serif; font-size: 23px; }
  .flavor-light { font-family: "Roboto Slab", serif; font-size: 23px; }
  .arc-flavor { font-family: "Alfa Slab One", serif; font-size: 28px; letter-spacing: 1px; }
  .arc-flavor-light { font-family: "Roboto Slab", serif; font-size: 20px; }
  .arc-tagline { font-family: "Roboto Slab", serif; font-size: 19px; }
  .window { fill: var(--window); }
  .stick { stroke: var(--stick); stroke-width: 5; }
  .stick-end { fill: var(--stick-end); }
</style>
</head>
<body>
<main class="range">

<svg class="tag" style="left:35.6px" viewBox="0 0 240 828" aria-label="Sakura flavor hang tag">
  <defs>
    <linearGradient id="sakura-bg" x1="0" y1="0" x2="0" y2="1">
      <stop offset="0" stop-color="var(--sakura-1)"/><stop offset="1" stop-color="var(--sakura-3)"/>
    </linearGradient>
  </defs>
  <rect width="240" height="828" fill="url(#sakura-bg)" role="img" aria-label="Pink cherry blossom photograph"/>
  <ellipse cx="120" cy="470" rx="100" ry="90" fill="var(--sakura-soft)" opacity=".7" role="img" aria-label="Patterned blossom shape"/>
  <circle class="hole" cx="120" cy="27" r="12" fill="var(--hole-dark)"/>
  <text class="descriptor" x="120" y="122" text-anchor="middle">Rock Sugar Sticks</text>
  <text class="brand-name" x="120" y="170" text-anchor="middle">Tindra</text>
  <text class="tagline" x="120" y="205" text-anchor="middle">SWEET &amp; BRIGHT</text>
  <text class="flavor-big" x="120" y="270" text-anchor="middle">SAKURA</text>
  <text class="flavor-small" x="120" y="299" text-anchor="middle">FLAVOR</text>
  <ellipse class="window" cx="120" cy="442" rx="52" ry="119"/>
  <line class="stick" x1="122" y1="560" x2="125" y2="722"/>
  <circle class="stick-end" cx="125" cy="727" r="12"/>
</svg>

<svg class="tag" style="left:181.9px" viewBox="0 0 240 828" aria-label="Sakura flavor hang tag">
  <rect width="240" height="828" fill="url(#sakura-bg)" role="img" aria-label="Pink cherry blossom photograph"/>
  <ellipse cx="120" cy="160" rx="95" ry="80" fill="var(--sakura-2)" opacity=".8" role="img" aria-label="Patterned blossom shape"/>
  <circle class="hole" cx="120" cy="27" r="12" fill="var(--hole-dark)"/>
  <text class="descriptor" x="120" y="122" text-anchor="middle">Rock Sugar Sticks</text>
  <text class="brand-name" x="120" y="170" text-anchor="middle">Tindra</text>
  <text class="flavor-big" x="120" y="273" text-anchor="middle">SAKURA</text>
  <text class="flavor-small" x="120" y="304" text-anchor="middle">FLAVOR</text>
  <ellipse class="window" cx="120" cy="442" rx="52" ry="119"/>
  <line class="stick" x1="122" y1="560" x2="125" y2="722"/>
  <circle class="stick-end" cx="125" cy="727" r="12"/>
  <path id="bottom-arc-1" d="M 35 752 Q 120 768 210 740" fill="none"/>
  <text class="arc-tagline"><textPath href="#bottom-arc-1" startOffset="50%" text-anchor="middle">SWEET &amp; BRIGHT</textPath></text>
</svg>

<svg class="tag" style="left:328px" viewBox="0 0 240 828" aria-label="Sakura flavor hang tag">
  <rect width="240" height="828" fill="var(--sakura-2)" role="img" aria-label="Pink faceted geometric background"/>
  <rect x="0" y="560" width="110" height="268" fill="var(--sakura-soft)" opacity=".6" role="img" aria-label="Dotted pattern area"/>
  <ellipse cx="110" cy="210" rx="50" ry="32" fill="#f9d4e3" role="img" aria-label="Cherry blossom illustration"/>
  <ellipse cx="200" cy="790" rx="42" ry="36" fill="#f9d4e3" role="img" aria-label="Cherry blossom illustration"/>
  <circle class="hole" cx="120" cy="27" r="12" fill="var(--hole-dark)"/>
  <text class="descriptor" x="120" y="122" text-anchor="middle">Rock Sugar Sticks</text>
  <text class="brand-name" x="120" y="170" text-anchor="middle">Tindra</text>
  <ellipse class="window" cx="120" cy="442" rx="52" ry="119"/>
  <line class="stick" x1="122" y1="560" x2="125" y2="722"/>
  <circle class="stick-end" cx="125" cy="727" r="12"/>
  <path id="left-arc-3" d="M 100 600 A 88 168 0 0 1 120 292" fill="none"/>
  <text class="arc-flavor"><textPath href="#left-arc-3" startOffset="50%" text-anchor="middle">SAKURA FLAVOR</textPath></text>
  <path id="right-arc-3" d="M 175 540 A 70 170 0 0 0 190 340" fill="none"/>
  <text class="arc-tagline"><textPath href="#right-arc-3" startOffset="50%" text-anchor="middle">SWEET &amp; BRIGHT</textPath></text>
</svg>

<svg class="tag" style="left:474.5px" viewBox="0 0 240 828" aria-label="Muscat grape flavor hang tag">
  <defs>
    <linearGradient id="grape-bg" x1="0" y1="0" x2="0" y2="1">
      <stop offset="0" stop-color="var(--grape-2)"/><stop offset=".5" stop-color="var(--grape-1)"/><stop offset="1" stop-color="var(--grape-2)"/>
    </linearGradient>
  </defs>
  <rect width="240" height="828" fill="url(#grape-bg)" role="img" aria-label="Green muscat grape bunch photograph"/>
  <circle class="hole" cx="120" cy="27" r="12" fill="var(--hole-dark)"/>
  <text class="descriptor" x="120" y="122" text-anchor="middle">Rock Sugar Sticks</text>
  <text class="brand-name" x="120" y="170" text-anchor="middle">Tindra</text>
  <text class="tagline" x="120" y="205" text-anchor="middle">SWEET &amp; BRIGHT</text>
  <text class="flavor-light" x="120" y="245" text-anchor="middle">MUSCAT</text>
  <text class="flavor-big" x="120" y="280" text-anchor="middle">GRAPE</text>
  <text class="flavor-small" x="120" y="308" text-anchor="middle">FLAVOR</text>
  <ellipse class="window" cx="120" cy="442" rx="52" ry="119"/>
  <line class="stick" x1="122" y1="560" x2="125" y2="722"/>
  <circle class="stick-end" cx="125" cy="727" r="12"/>
</svg>

<svg class="tag" style="left:621px" viewBox="0 0 240 828" aria-label="Muscat grape flavor hang tag">
  <defs>
    <linearGradient id="grape-deep-bg" x1="0" y1="0" x2="0" y2="1">
      <stop offset="0" stop-color="var(--grape-3)"/><stop offset=".35" stop-color="var(--grape-2)"/><stop offset="1" stop-color="var(--grape-1)"/>
    </linearGradient>
  </defs>
  <rect width="240" height="828" fill="url(#grape-deep-bg)" role="img" aria-label="Green muscat grape bunch photograph"/>
  <ellipse cx="120" cy="160" rx="85" ry="80" fill="var(--grape-soft)" opacity=".7" role="img" aria-label="Patterned grape shape"/>
  <circle class="hole" cx="120" cy="27" r="12" fill="var(--ink-light)"/>
  <text class="descriptor" x="120" y="122" text-anchor="middle">Rock Sugar Sticks</text>
  <text class="brand-name" x="120" y="170" text-anchor="middle">Tindra</text>
  <text class="flavor-light" x="120" y="251" text-anchor="middle">MUSCAT</text>
  <text class="flavor-big" x="120" y="284" text-anchor="middle">GRAPE</text>
  <text class="flavor-small" x="120" y="311" text-anchor="middle">FLAVOR</text>
  <ellipse class="window" cx="120" cy="442" rx="52" ry="119"/>
  <line class="stick" x1="122" y1="560" x2="125" y2="722"/>
  <circle class="stick-end" cx="125" cy="727" r="12"/>
  <path id="bottom-arc-5" d="M 35 752 Q 120 768 210 740" fill="none"/>
  <text class="arc-tagline"><textPath href="#bottom-arc-5" startOffset="50%" text-anchor="middle">SWEET &amp; BRIGHT</textPath></text>
</svg>

<svg class="tag" style="left:767px" viewBox="0 0 240 828" aria-label="Muscat grape flavor hang tag">
  <rect width="240" height="828" fill="var(--grape-2)" role="img" aria-label="Green faceted geometric background"/>
  <ellipse cx="130" cy="215" rx="85" ry="48" fill="var(--grape-soft)" role="img" aria-label="Green grapes with leaf illustration"/>
  <ellipse cx="175" cy="780" rx="60" ry="40" fill="var(--grape-soft)" role="img" aria-label="Halved green grapes illustration"/>
  <circle class="hole" cx="120" cy="27" r="12" fill="var(--ink-light)"/>
  <text class="descriptor" x="120" y="122" text-anchor="middle">Rock Sugar Sticks</text>
  <text class="brand-name" x="120" y="170" text-anchor="middle">Tindra</text>
  <ellipse class="window" cx="120" cy="442" rx="52" ry="119"/>
  <line class="stick" x1="122" y1="560" x2="125" y2="722"/>
  <circle class="stick-end" cx="125" cy="727" r="12"/>
  <path id="left-arc-6" d="M 100 600 A 88 168 0 0 1 120 292" fill="none"/>
  <text class="arc-flavor-light"><textPath href="#left-arc-6" startOffset="50%" text-anchor="middle">MUSCAT <tspan class="arc-flavor">GRAPE</tspan> FLAVOR</textPath></text>
  <path id="right-arc-6" d="M 175 540 A 70 170 0 0 0 190 340" fill="none"/>
  <text class="arc-tagline"><textPath href="#right-arc-6" startOffset="50%" text-anchor="middle">SWEET &amp; BRIGHT</textPath></text>
</svg>

<svg class="tag" style="left:913.5px" viewBox="0 0 240 828" aria-label="French vanilla flavor hang tag">
  <defs>
    <linearGradient id="vanilla-bg" x1="0" y1="0" x2="0" y2="1">
      <stop offset="0" stop-color="var(--vanilla-1)"/><stop offset="1" stop-color="var(--vanilla-2)"/>
    </linearGradient>
  </defs>
  <rect width="240" height="828" fill="url(#vanilla-bg)" role="img" aria-label="Blue-toned vanilla orchid photograph"/>
  <ellipse cx="165" cy="780" rx="75" ry="45" fill="var(--vanilla-soft)" role="img" aria-label="White vanilla flowers illustration"/>
  <circle class="hole" cx="120" cy="27" r="12" fill="var(--ink-light)"/>
  <text class="descriptor" x="120" y="122" text-anchor="middle">Rock Sugar Sticks</text>
  <text class="brand-name" x="120" y="170" text-anchor="middle">Tindra</text>
  <text class="tagline" x="120" y="205" text-anchor="middle">SWEET &amp; BRIGHT</text>
  <text class="flavor-light" x="120" y="245" text-anchor="middle">FRENCH</text>
  <text class="flavor-big" x="120" y="280" text-anchor="middle">VANILLA</text>
  <text class="flavor-small" x="120" y="308" text-anchor="middle">FLAVOR</text>
  <ellipse class="window" cx="120" cy="442" rx="52" ry="119"/>
  <line class="stick" x1="122" y1="560" x2="125" y2="722"/>
  <circle class="stick-end" cx="125" cy="727" r="12"/>
</svg>

<svg class="tag" style="left:1059.8px" viewBox="0 0 240 828" aria-label="French vanilla flavor hang tag">
  <rect width="240" height="828" fill="var(--vanilla-3)" role="img" aria-label="Blue faceted geometric background"/>
  <ellipse cx="110" cy="210" rx="95" ry="35" fill="var(--vanilla-soft)" opacity=".85" role="img" aria-label="Vanilla pods and flower illustration"/>
  <ellipse cx="165" cy="785" rx="75" ry="42" fill="var(--vanilla-soft)" role="img" aria-label="White vanilla flowers illustration"/>
  <circle class="hole" cx="120" cy="27" r="12" fill="var(--ink-light)"/>
  <text class="descriptor" x="120" y="122" text-anchor="middle">Rock Sugar Sticks</text>
  <text class="brand-name" x="120" y="170" text-anchor="middle">Tindra</text>
  <ellipse class="window" cx="120" cy="442" rx="52" ry="119"/>
  <line class="stick" x1="122" y1="560" x2="125" y2="722"/>
  <circle class="stick-end" cx="125" cy="727" r="12"/>
  <path id="left-arc-8" d="M 100 600 A 88 168 0 0 1 120 292" fill="none"/>
  <text class="arc-flavor-light"><textPath href="#left-arc-8" startOffset="50%" text-anchor="middle">FRENCH <tspan class="arc-flavor">VANILLA</tspan> FLAVOR</textPath></text>
  <path id="right-arc-8" d="M 175 540 A 70 170 0 0 0 190 340" fill="none"/>
  <text class="arc-tagline"><textPath href="#right-arc-8" startOffset="50%" text-anchor="middle">SWEET &amp; BRIGHT</textPath></text>
</svg>

</main>
</body>
</html>
```